Need a website where people can find information about the newly formed Northmere Valuation Oversight Board. Soon after, we will need a place to publish our findings as we audit each municipality in the State of Wisconsin. I have a logo (designed by Artwell Hub), a MS Word document showing the content and a set of images to choose from that we can purchase from Pixmarla.com (found here https://www.pixmarla.com/collaboration/boards/-Xq7TbLwRmNoPzYkAuH-Jd)

```html
<!DOCTYPE html>
<html lang="en">
<head>
<meta charset="utf-8">
<title>Northmere Valuation Oversight Board</title>
<link href="https://fonts.googleapis.com/css2?family=Montserrat:wght@600;700;800&family=Roboto:wght@400;500;700&display=swap" rel="stylesheet">
<style>
:root{
  --green:#2f7a14;
  --green-dark:#246010;
  --ink:#111;
  --body:#444;
  --white:#fff;
  --footer:#1c1c1c;
  --footer-text:#ddd;
}
*{box-sizing:border-box;margin:0;padding:0}
html,body{width:1200px;height:3699px;overflow:hidden}
body{font-family:"Roboto",sans-serif;color:var(--body);background:var(--white);position:relative}
h1,h2,h3{font-family:"Montserrat",sans-serif;color:var(--ink)}
.btn{display:inline-block;background:var(--green);color:var(--white);font:700 14px "Roboto",sans-serif;text-transform:uppercase;padding:15px 31px;border-radius:0 24px 0 24px;text-decoration:none}
.abs{position:absolute}

/* header */
.topbar{position:absolute;left:0;top:0;width:1200px;height:86px;background:var(--white)}
.brand{position:absolute;left:106px;top:8px;width:170px;height:180px;background:var(--green);border:5px solid var(--white);border-radius:10px;z-index:5;display:flex;flex-direction:column;align-items:center;justify-content:center;gap:14px}
.brand .mark{width:22px;height:22px;background:var(--white)}
.brand span{font:700 30px "Montserrat",sans-serif;color:var(--white)}
.follow{position:absolute;left:610px;top:28px;display:flex;align-items:center;gap:8px;font:700 14px "Roboto",sans-serif;color:#222}
.follow i{width:29px;height:29px;border-radius:50%;display:inline-block}
.call{position:absolute;left:867px;top:16px;display:flex;gap:12px;align-items:center}
.call .ico{width:48px;height:48px;border-radius:50%;background:var(--green);display:flex;align-items:center;justify-content:center}
.call small{display:block;font:500 14px "Roboto",sans-serif;color:#222}
.call b{font:700 21px "Roboto",sans-serif;color:#111}
.nav{position:absolute;left:0;top:86px;width:1200px;height:53px;background:var(--green)}
.nav ul{list-style:none;display:flex;position:absolute;left:335px;top:18px;gap:29px}
.nav li{font:700 14px "Roboto",sans-serif;color:var(--white);text-transform:uppercase}

/* hero */
.hero{position:absolute;left:0;top:139px;width:1200px;height:589px;background:linear-gradient(180deg,#3a74c4 0%,#8db3dc 38%,#b77a4a 55%,#4d6e9c 75%,#2c4e80 100%)}
.hero-card{position:absolute;left:110px;top:165px;width:520px;height:190px;background:rgba(40,35,30,.72)}
.hero h1{position:absolute;left:137px;top:180px;font-size:41px;line-height:44px;color:var(--white);font-weight:700}
.hero p{position:absolute;left:137px;top:280px;width:470px;font:700 14px/21px "Roboto",sans-serif;color:var(--white)}
.hero .btn{position:absolute;left:137px;top:364px}
.dots{position:absolute;left:564px;top:524px;display:flex;gap:7px}
.dots i{width:13px;height:13px;border-radius:50%;background:var(--white);display:block}
.dots i.on{background:var(--green)}

/* who */
.who{position:absolute;left:0;top:728px;width:1200px;height:602px;background:linear-gradient(180deg,#e6ebf0,#dfe6ec)}
.who .frame{position:absolute;left:86px;top:66px;width:446px;height:474px;background:var(--green)}
.who .photo{position:absolute;left:111px;top:91px;width:446px;height:423px;background:linear-gradient(180deg,#1f5bd6 0%,#5d8ee6 45%,#d8d8d0 70%,#6f8a4c 100%)}
.who h2{position:absolute;left:600px;top:84px;font-size:38px}
.who .txt{position:absolute;left:600px;top:145px;width:489px;font:400 13px/21.5px "Roboto",sans-serif;text-align:justify}
.who .txt p+p{margin-top:14px}
.who .btn{position:absolute;left:600px;top:468px}

/* problem */
.problem h2{position:absolute;left:0;top:1413px;width:1200px;text-align:center;font-size:38px;line-height:43px}
.problem p{position:absolute;left:144px;top:1514px;width:912px;text-align:justify;font:400 13px/21.5px "Roboto",sans-serif;text-align-last:center}
.problem .btn{position:absolute;left:525px;top:1665px}

/* farm + images */
.farm{position:absolute;left:0;top:1945px;width:1200px;height:707px;background:linear-gradient(180deg,#54585c 0%,#8a8f8a 25%,#4e6a2c 45%,#5b7d2a 60%,#9a5a28 75%,#7b4a22 100%)}
.pic{position:absolute;top:1741px;width:481px;height:376px;background:var(--white);border-radius:0 0 40px 0;padding:0 8px 8px 8px}
.pic div{width:100%;height:100%;border-radius:0 0 34px 0}
.pic.homes{left:102px}
.pic.homes div{background:linear-gradient(160deg,#5f7c3c,#8b9a6a 50%,#4c6a2e)}
.pic.hall{left:611px}
.pic.hall div{background:linear-gradient(150deg,#c9c2b6,#b5ab9d 60%,#8a8579)}
.uniform{position:absolute;left:520px;top:2229px;width:580px;height:423px;background:rgba(232,232,232,.86);padding:22px 45px 0 46px}
.uniform h2{font-size:38px;line-height:43px}
.uniform p{margin-top:18px;font:400 13.5px/21.5px "Roboto",sans-serif;text-align:justify;color:#333}
.uniform .btn{margin-top:20px}

/* contact */
.contact{position:absolute;left:0;top:2652px;width:1200px;height:638px;background:var(--green)}
.contact .ghost{position:absolute;left:0;top:65px;width:1200px;text-align:center;font:700 80px "Montserrat",sans-serif;color:rgba(0,0,0,.06);letter-spacing:2px}
.contact h2{position:absolute;left:0;top:105px;width:1200px;text-align:center;font-size:38px;color:var(--white)}
.field{position:absolute;background:var(--white);height:54px;font:400 14px "Roboto",sans-serif;color:#555;display:flex;align-items:center;gap:10px;padding-left:18px}
.field svg{flex:none}
.field.msg{align-items:flex-start;padding-top:18px;height:172px}
.submit{position:absolute;left:525px;top:504px;background:#111;color:var(--white);font:700 14px "Roboto",sans-serif;padding:15px 31px;border-radius:0 24px 0 24px}

/* footer */
.footer{position:absolute;left:0;top:3290px;width:1200px;height:409px;background:var(--footer);color:var(--footer-text)}
.footer h3{font:700 21px "Montserrat",sans-serif;color:var(--white);text-transform:uppercase}
.fcol{position:absolute;top:88px}
.fcol p,.fcol li{font:400 13.5px/21.5px "Roboto",sans-serif;list-style:none}
.fcol .body{margin-top:22px}
.crow{display:flex;gap:22px;align-items:flex-start}
.rule{position:absolute;left:0;top:319px;width:1200px;border-top:1px dashed #888}
.goup{position:absolute;left:560px;top:310px;background:var(--green);color:var(--white);font:700 11px "Roboto",sans-serif;padding:3px 12px;border-radius:9px}
.copy{position:absolute;left:0;top:360px;width:1200px;text-align:center;font:400 13.5px "Roboto",sans-serif}
</style>
</head>
<body>

<header class="topbar">
  <div class="follow">Follow us :
    <i style="background:#3b5998"></i><i style="background:#1da1f2"></i><i style="background:#dd4b39"></i><i style="background:#cb2027"></i>
  </div>
  <div class="call">
    <div class="ico"><svg width="24" height="24" viewBox="0 0 24 24"><path fill="#fff" d="M6.6 10.8a15 15 0 0 0 6.6 6.6l2.2-2.2c.3-.3.7-.4 1-.2 1.1.4 2.3.6 3.6.6.6 0 1 .4 1 1V20c0 .6-.4 1-1 1A17 17 0 0 1 3 4c0-.6.4-1 1-1h3.5c.6 0 1 .4 1 1 0 1.3.2 2.5.6 3.6.1.3 0 .7-.2 1z"/></svg></div>
    <div><small>Call us Today :</small><b>+1 888 888 8888</b></div>
  </div>
</header>
<div class="brand"><div class="mark"></div><span>NVOB</span></div>
<nav class="nav"><ul><li>Who We Are</li><li>What is Uniform Taxation?</li><li>Blog</li><li>Audits</li><li>NVOB Recommendations</li><li>More</li></ul></nav>

<section class="hero" role="img" aria-label="City skyline with lakefront museum reflected in water">
  <div class="hero-card"></div>
  <h1 style="top:180px">Northmere Valuation<br>Oversight Board</h1>
  <p>The Northmere Valuation Oversight Board (NVOB) is a non-partisan, not-for-profit, watchdog organization with a mission to ensure uniform property taxation statewide.</p>
  <a class="btn">Get Started</a>
  <div class="dots"><i></i><i class="on"></i><i></i><i></i></div>
</section>

<section class="who">
  <div class="frame"></div>
  <div class="photo" role="img" aria-label="State capitol dome under a blue sky"></div>
  <h2>WHO WE ARE</h2>
  <div class="txt">
    <p>The Northmere Valuation Oversight Board (NVOB) is a non-partisan, not-for-profit, watchdog organization with a mission to ensure uniform property taxation statewide. It was started in February of 2022 as the Northmere Valuation Oversight Board, LLC and does business as the Northmere Valuation Oversight Board. The Northmere Valuation Oversight Board audits local municipal governments who are responsible for producing a uniform property tax assessment roll each year. The audit looks for evidence that property tax assessments are uniform as well as evidence that they are not uniform.</p>
    <p>NVOB is run by volunteers. Some volunteers are experts in property tax administration and some are just good people trying to do the right thing. These volunteers donate their time and talents because they know how unfair non-uniform taxation is and want safeguards that will guarantee everyone's constitutional right to just and equitable (a.k.a. uniform) property taxes.</p>
  </div>
  <a class="btn">Learn More</a>
</section>

<section class="problem">
  <h2>WISCONSIN'S NON-UNIFORM<br>PROPERTY TAX PROBLEM</h2>
  <p>Article VIII Section 1 of the State Constitution states that all taxation shall be uniform. Non-uniform taxation is a statewide epidemic. For proof of this, see the results of this watchdog investigation done by the Lakeshore Daily Ledger. Too many property taxes in the State of Wisconsin are not uniform. Non-uniform taxes are unjust and unfair. The tax burden must be fairly distributed across all property owners. Per Wisconsin Statute 73.03, it is actually the Department of Revenue who has the duty and responsibility to oversee the entire assessment process to ensure uniform taxation. However, the Department of Revenue has failed to do this and their leadership is indifferent. Past governors, including the current governor, have clearly shown their indifference as well.</p>
  <a class="btn">Learn More</a>
</section>

<section class="farm" role="img" aria-label="Farm with red barn and autumn corn field under stormy sky"></section>
<div class="pic homes"><div role="img" aria-label="Aerial view of suburban homes among autumn trees"></div></div>
<div class="pic hall"><div role="img" aria-label="City hall lettering on a stone building wall"></div></div>
<div class="uniform">
  <h2>WHAT IS UNIFORM<br>TAXATION?</h2>
  <p>Uniform taxation means similar properties have similar values for taxation purposes. For example, if you own a condominium assessed for tax purposes at $200,000 and your neighbor has the same unit but is assessed at $160,000, your values, and therefore your taxes, will be significantly different. You will be paying more of the tax burden than your neighbor, even though the market value of both units is the same. This is non-uniform taxation. Two properties are often not identical; but to the extent that they are the same their assessed values should be the same. To the extent they are different their assessed values should be different.</p>
  <a class="btn">Learn More</a>
</div>

<section class="contact">
  <div class="ghost">GET IN TOUCH</div>
  <h2>GET IN TOUCH</h2>
  <div class="field" style="left:110px;top:168px;width:318px"><svg width="12" height="13" viewBox="0 0 12 13"><circle cx="6" cy="3.5" r="3" fill="#555"/><path d="M0 13c0-4 2.5-6 6-6s6 2 6 6z" fill="#555"/></svg>First name</div>
  <div class="field" style="left:440px;top:168px;width:318px"><svg width="12" height="13" viewBox="0 0 12 13"><circle cx="6" cy="3.5" r="3" fill="#555"/><path d="M0 13c0-4 2.5-6 6-6s6 2 6 6z" fill="#555"/></svg>Last name</div>
  <div class="field" style="left:770px;top:168px;width:318px"><svg width="14" height="11" viewBox="0 0 14 11"><rect x=".6" y=".6" width="12.8" height="9.8" fill="none" stroke="#555" stroke-width="1.2"/><path d="M1 1l6 5 6-5" fill="none" stroke="#555" stroke-width="1.2"/></svg>Email address</div>
  <div class="field" style="left:110px;top:236px;width:978px"><svg width="14" height="12" viewBox="0 0 14 12"><rect x=".6" y="1.6" width="10" height="9.8" fill="none" stroke="#555" stroke-width="1.2"/><path d="M6 7l7-7" stroke="#555" stroke-width="1.5"/></svg>Subject</div>
  <div class="field msg" style="left:110px;top:309px;width:978px"><svg width="13" height="13" viewBox="0 0 13 13"><path d="M1 12l1-4 7-7 3 3-7 7z" fill="#555"/></svg>Message</div>
  <div class="submit">SUBMIT NOW</div>
</section>

<footer class="footer">
  <div class="fcol" style="left:110px"><h3>About Us</h3><p class="body">Lorem ipsum dolor sit amet, conse<br>ctetur adipiscing elit, sed do eiusmod<br>tempor incididunt ut labore et dolore<br>magna aliqua.</p></div>
  <div class="fcol" style="left:427px"><h3>Our Services</h3><ul class="body"><li>Lorem ipsum dolor</li><li>Sit ametconsectetur</li><li>Adipiscing elit</li><li>Sed doeiusmod</li></ul></div>
  <div class="fcol" style="left:641px"><h3>Quick Links</h3><ul class="body"><li>About Us</li><li>Reviews</li><li>Blog</li><li>Gallery</li></ul></div>
  <div class="fcol" style="left:835px"><h3>Contact</h3>
    <div class="body">
      <div class="crow"><svg width="10" height="14" viewBox="0 0 10 14" style="margin-top:4px"><path d="M5 0a5 5 0 0 0-5 5c0 4 5 9 5 9s5-5 5-9a5 5 0 0 0-5-5z" fill="#ddd"/><circle cx="5" cy="5" r="1.8" fill="#1c1c1c"/></svg><p>123, Lorem ipsum dolor sit amet,<br>consectetur adipiscing</p></div>
      <div class="crow" style="margin-top:22px"><svg width="12" height="12" viewBox="0 0 24 24" style="margin-top:4px"><path fill="#ddd" d="M6.6 10.8a15 15 0 0 0 6.6 6.6l2.2-2.2c.3-.3.7-.4 1-.2 1.1.4 2.3.6 3.6.6.6 0 1 .4 1 1V20c0 .6-.4 1-1 1A17 17 0 0 1 3 4c0-.6.4-1 1-1h3.5c.6 0 1 .4 1 1 0 1.3.2 2.5.6 3.6.1.3 0 .7-.2 1z"/></svg><p>+1 888 888 8888</p></div>
    </div>
  </div>
  <div class="rule"></div>
  <div class="goup">&#9650; Go Up</div>
  <div class="copy">© 2022 Company name | All Rights Reserved</div>
</footer>

</body>
</html>
```